Veldmark Supplies Business Card

Professional business card that stand out to our potential customers. Front and back with clean modern design

Industry/Entity Type

Oil and gas

Contact Information for Business Card

Name, address, website , office phone and cell number

Requirements
Must have
• Editable files for each employee

```html
<!DOCTYPE html>
<html lang="en">
<head>
<meta charset="utf-8">
<title>Veldmark Supplies Business Card</title>
<link rel="stylesheet" href="https://fonts.googleapis.com/css2?family=Montserrat:wght@400;500;700;800&display=swap">
<style>
  :root {
    --brand-red: #ec2027;
    --brand-cyan: #08aed0;
    --paper: #ffffff;
    --backdrop: #2e2c2a;
    --shadow: rgba(0,0,0,0.45);
  }
  * { box-sizing: border-box; margin: 0; padding: 0; }
  html, body { width: 1200px; height: 900px; overflow: hidden; }
  body {
    background: var(--backdrop);
    font-family: "Montserrat", Arial, sans-serif;
    position: relative;
  }
  .card {
    position: absolute;
    width: 700px;
    height: 400px;
    border-radius: 26px;
    overflow: hidden;
    box-shadow: 0 12px 28px var(--shadow);
  }
  .card-front {
    left: 90px;
    top: 40px;
    background: var(--brand-red);
  }
  .card-back {
    left: 410px;
    top: 470px;
    background: var(--paper);
  }
  .wordmark {
    position: absolute;
    display: flex;
    align-items: center;
    font-weight: 800;
    text-transform: uppercase;
    white-space: nowrap;
  }
  .wordmark-square {
    display: block;
    flex: none;
  }
  .card-front .wordmark {
    left: 0; right: 0;
    top: 170px;
    gap: 14px;
    justify-content: center;
    color: var(--paper);
    font-size: 40px;
    letter-spacing: 2px;
  }
  .card-front .wordmark-square {
    width: 34px; height: 34px;
    background: var(--paper);
  }
  .card-back .wordmark {
    left: 50px;
    top: 140px;
    gap: 12px;
    color: var(--brand-red);
    font-size: 21px;
    letter-spacing: 1px;
  }
  .card-back .wordmark-square {
    width: 20px; height: 20px;
    background: var(--brand-red);
  }
  .swoosh {
    position: absolute;
    inset: 0;
    width: 700px;
    height: 400px;
  }
  .contact {
    position: absolute;
    right: 34px;
    top: 150px;
    width: 300px;
    color: var(--paper);
    text-align: right;
  }
  .contact-name {
    font-weight: 700;
    font-size: 17px;
    letter-spacing: 0.5px;
    text-transform: uppercase;
  }
  .contact-title {
    font-size: 13px;
    font-weight: 500;
    margin-bottom: 14px;
  }
  .contact-address {
    font-size: 12.5px;
    line-height: 1.35;
    margin-bottom: 8px;
  }
  .contact-line {
    display: flex;
    justify-content: flex-end;
    align-items: center;
    gap: 10px;
    font-size: 12.5px;
    height: 22px;
  }
  .contact-icon {
    width: 18px; height: 18px;
    background: var(--brand-cyan);
    display: flex;
    align-items: center;
    justify-content: center;
    flex: none;
  }
  .contact-icon svg { width: 12px; height: 12px; }
</style>
</head>
<body>

  <section class="card card-front" aria-label="Business card front">
    <div class="wordmark">
      <span class="wordmark-square"></span>
      <span class="wordmark-name">Veldmark Supplies</span>
    </div>
  </section>

  <section class="card card-back" aria-label="Business card back">
    <svg class="swoosh" viewBox="0 0 700 400" aria-hidden="true">
      <defs>
        <path id="wave-area" d="M0,335 C260,335 390,260 460,150 C520,60 590,20 700,0 L700,400 L0,400 Z"/>
        <path id="wave-line" d="M0,335 C260,335 390,260 460,150 C520,60 590,20 700,0"/>
      </defs>
      <use href="#wave-line" transform="translate(0,-30)" fill="none" stroke="var(--brand-red)" stroke-width="4"/>
      <use href="#wave-area" transform="translate(0,-20)" fill="var(--brand-cyan)"/>
      <use href="#wave-area" transform="translate(0,-6)" fill="var(--paper)"/>
      <use href="#wave-area" fill="var(--brand-red)"/>
    </svg>

    <div class="wordmark">
      <span class="wordmark-square"></span>
      <span class="wordmark-name">Veldmark Supplies</span>
    </div>

    <div class="contact">
      <p class="contact-name">Dana Whitfield</p>
      <p class="contact-title">President</p>
      <p class="contact-address">2450 Harwood Lane, Ste 210<br>Midland, TX 79701</p>
      <p class="contact-line">432-555-0148
        <span class="contact-icon"><svg viewBox="0 0 12 12"><path d="M1,4 Q6,0 11,4 L10,6 L8,5 L8,4 Q6,3 4,4 L4,5 L2,6 Z M3,7 L9,7 L10,11 L2,11 Z" fill="#fff"/></svg></span>
      </p>
      <p class="contact-line">432-555-0176
        <span class="contact-icon"><svg viewBox="0 0 12 12"><rect x="3" y="0.5" width="6" height="11" rx="1" fill="none" stroke="#fff" stroke-width="1.2"/><circle cx="6" cy="9.5" r="0.7" fill="#fff"/></svg></span>
      </p>
      <p class="contact-line">info@veldmarksupplies.com
        <span class="contact-icon"><svg viewBox="0 0 12 12"><rect x="0.8" y="2.5" width="10.4" height="7" fill="none" stroke="#fff" stroke-width="1.1"/><path d="M0.8,2.5 L6,7 L11.2,2.5" fill="none" stroke="#fff" stroke-width="1.1"/></svg></span>
      </p>
      <p class="contact-line">www.veldmarksupplies.com
        <span class="contact-icon"><svg viewBox="0 0 12 12"><circle cx="6" cy="6" r="5" fill="none" stroke="#fff" stroke-width="1.1"/><ellipse cx="6" cy="6" rx="2" ry="5" fill="none" stroke="#fff" stroke-width="0.9"/><path d="M1,6 L11,6" stroke="#fff" stroke-width="0.9"/></svg></span>
      </p>
    </div>
  </section>

</body>
</html>
```